Brintel Works - Fast, Efficient and Gas Mainteance for Domestic, Commercial and Industrial clients

We are in the process of purchasing a new business and would like to get a new logo and business card.
Business is a gas maintenance business that also does new gas installations.
Has been established since 1988.
Services include:
Install all types of gas appliances & equipment inc. hot water units
Maintain / repair / replace all types of gas appliances & equipment

Target Market(s)

Domestic, Commercial and Industrial clients

Industry/Entity Type

Business

Contact Information for Business Card

admin@brintelworks.com.au
07 3918 4726
Brintel Works PTY LTD

Logo Text

Gas Fitting & Plumbing Maintenance Specialists

Font styles to use
Sans Serif

Requirements
Must have
• Logo
• Business name, contact number, email address, web address
• Domestic | Commercial | Industrial Est Since 1988
Nice to have
• Possibly a black card with a flame logo to one side
Should not have
• Spelling errors

```html
<!DOCTYPE html>
<html lang="en">
<head>
<meta charset="utf-8">
<title>Brintel Works – Business Card</title>
<link href="https://fonts.googleapis.com/css2?family=Cinzel:wght@600&family=Open+Sans:wght@400;600&family=Arimo:wght@400&family=Great+Vibes&display=swap" rel="stylesheet">
<style>
  :root {
    --page-bg: #e9e7e3;
    --card-black: #0b0b0b;
    --card-white: #f3f3f3;
    --brand-red: #e04a36;
    --slate: #3f4654;
    --muted: #8a8f98;
    --ink: #111111;
  }
  * { margin: 0; padding: 0; box-sizing: border-box; }
  html, body { width: 1200px; height: 902px; overflow: hidden; background: var(--page-bg); }
  .canvas {
    width: 1200px; height: 902px;
    display: flex; align-items: center; justify-content: center; gap: 40px;
  }
  .card {
    width: 520px; height: 318px;
    border-radius: 4px;
    box-shadow: 0 6px 18px rgba(0,0,0,.18);
    position: relative; overflow: hidden;
  }
  /* Front */
  .card--front { background: var(--card-black); display: flex; align-items: center; justify-content: center; }
  .front-name { display: flex; align-items: baseline; gap: 12px; }
  .front-name__title {
    font-family: "Cinzel", serif; font-weight: 600;
    font-size: 38px; color: var(--brand-red); letter-spacing: 1px;
  }
  .front-name__suffix {
    font-family: "Cinzel", serif; font-weight: 600;
    font-size: 17px; color: var(--muted); letter-spacing: 1px;
  }
  /* Back */
  .card--back { background: var(--card-white); padding: 34px 34px 0 34px; }
  .brand { display: flex; align-items: flex-start; gap: 14px; }
  .brand__dot { width: 44px; height: 44px; border-radius: 50%; background: #d9d9d9; margin-top: 20px; flex: none; }
  .brand__text { flex: 1; }
  .brand__name-row { display: flex; align-items: flex-start; gap: 6px; }
  .brand__name {
    font-family: "Cinzel", serif; font-weight: 600;
    font-size: 33px; line-height: 1; color: var(--brand-red);
  }
  .brand__suffix {
    font-family: "Cinzel", serif; font-weight: 600;
    font-size: 9px; color: var(--muted); margin-top: 2px;
  }
  .brand__tagline {
    font-family: "Open Sans", sans-serif; font-weight: 600;
    font-size: 19px; color: var(--slate); margin-top: 6px;
  }
  .brand__meta { display: flex; align-items: baseline; justify-content: space-between; margin-top: 2px; }
  .brand__sectors {
    font-family: "Open Sans", sans-serif; font-size: 11.5px; color: var(--muted);
  }
  .brand__est {
    font-family: "Great Vibes", cursive; font-size: 22px; color: var(--muted);
  }
  .rule { height: 2px; background: var(--brand-red); margin: 12px 0 16px; }
  .contact {
    font-family: "Arimo", sans-serif; font-size: 19px; color: var(--ink);
    text-align: center; line-height: 1.5;
  }
  .contact__gap { height: 10px; }
</style>
</head>
<body>
<main class="canvas">
  <section class="card card--front" aria-label="Card front">
    <div class="front-name">
      <span class="front-name__title">BRINTEL WORKS</span>
      <span class="front-name__suffix">PTY LTD</span>
    </div>
  </section>

  <section class="card card--back" aria-label="Card back">
    <div class="brand">
      <span class="brand__dot"></span>
      <div class="brand__text">
        <div class="brand__name-row">
          <span class="brand__name">BRINTEL WORKS</span>
          <span class="brand__suffix">PTY LTD</span>
        </div>
        <p class="brand__tagline">Gas fitting &amp; Plumbing Specialists</p>
        <div class="brand__meta">
          <span class="brand__sectors">Domestic | Commercial | Industrial</span>
          <span class="brand__est">Est Since 1988</span>
        </div>
      </div>
    </div>
    <div class="rule"></div>
    <div class="contact">
      <p>07 3918 4726</p>
      <p>04 2853 1790</p>
      <div class="contact__gap"></div>
      <p>admin@brintelworks.com.au</p>
      <p>www.brintelworks.com.au</p>
    </div>
  </section>
</main>
</body>
</html>
```